Hong Kong based International Remittance and ForEx company requires website design

We need a website designed for a new European - Hong Kong based ForEx & fund remittence entity.

The company specialises in larger corporate & high net worth private client trades, therefore the design must aesthetically reflect this (sophisticated). As a theme colour, financial entities tend to use either blue or red; if blue, our preference is a darker blue. Visually, our preference is less copy, more imagery.

Number of pages would be limited; landing (home), about us, client registration (x1 Corporate form, x1 Private Client form), Contact Us.

Have uploaded the existing logo - please note this is to be redesigned, although the colour scheme will remain the same. Please also note that copy will follow - please use Lorem Ipsum.

Target Market(s)

Medium to large Corporations. High net worth individuals.

Industry/Entity Type

Financial Service

Coding

Coded - Design and coding required

Number of Pages Required

4 page

Font styles to use
Serif

Requirements
Nice to have
• ForEx ticker,

```html
<!DOCTYPE html>
<html lang="en">
<head>
<meta charset="utf-8">
<title>Harbourline Incorporation Limited</title>
<link rel="stylesheet" href="https://fonts.googleapis.com/css2?family=Open+Sans:ital,wght@0,400;0,600;0,700;1,400&display=swap">
<style>
:root{
  --blue:#1f6db3;
  --blue-dark:#175a96;
  --blue-deep:#1a4f80;
  --nav-active:#2b1d16;
  --ink:#333a40;
  --white:#ffffff;
  --footer:#231914;
  --line:#e3e7eb;
  --up:#2f9a3a;
  --down:#d33b2c;
}
*{box-sizing:border-box;margin:0;padding:0}
html,body{width:1200px;height:2466px;overflow:hidden}
body{font-family:"Open Sans",Arial,sans-serif;color:var(--ink);background:var(--white);position:relative}

/* header */
.site-header{position:absolute;left:0;top:0;width:1200px;height:156px;background:var(--white)}
.brand{position:absolute;left:99px;top:58px;display:flex;align-items:center;gap:12px}
.brand-mark{width:34px;height:34px;border-radius:50%;background:var(--blue)}
.brand-name{font-size:30px;font-weight:600;color:#2c2c2c;line-height:1}
.brand-sub{position:absolute;left:145px;top:96px;font-size:10px;letter-spacing:3px;color:#2c2c2c;font-weight:600}
.contact-item{position:absolute;top:44px;display:flex;gap:14px}
.contact-item svg{flex:none}
.contact-label{font-size:13px;color:#444;margin-bottom:6px}
.contact-value{font-size:16px;color:#444}
.contact-address{font-size:12.5px;color:#444;line-height:25px}

/* nav */
.main-nav{position:absolute;left:0;top:156px;width:1200px;height:58px;background:linear-gradient(#2676bf,#1b62a6)}
.nav-item{position:absolute;top:0;height:58px;line-height:58px;color:var(--white);font-size:12.5px;text-transform:uppercase}
.nav-item.active{left:99px;width:136px;background:var(--nav-active);text-align:center}
.caret{display:inline-block;margin-left:12px;width:6px;height:6px;border-right:1.5px solid #fff;border-bottom:1.5px solid #fff;transform:rotate(45deg) translateY(-4px)}
.dropdown{position:absolute;left:500px;top:224px;width:210px;background:var(--white);box-shadow:0 2px 6px rgba(0,0,0,.2);padding:4px 14px;z-index:5}
.dropdown li{list-style:none;font-size:11.5px;color:#555;height:26px;line-height:26px;border-bottom:1px solid var(--line)}
.dropdown li:last-child{border-bottom:0}
.dropdown li::before{content:"›";margin-right:7px;color:#555}

/* hero */
.hero{position:absolute;left:0;top:214px;width:1200px;height:513px;
  background:
    radial-gradient(ellipse 260px 420px at 780px 300px,rgba(40,70,110,.55),rgba(40,70,110,0) 70%),
    radial-gradient(ellipse 420px 200px at 260px 440px,rgba(70,80,95,.6),rgba(70,80,95,0) 75%),
    radial-gradient(ellipse 200px 260px at 1150px 300px,rgba(60,90,130,.5),rgba(60,90,130,0) 70%),
    linear-gradient(180deg,#2f7fd0 0%,#5aa2e4 30%,#8fbfe6 44%,#6f8fb0 52%,#3d7fb8 62%,#2a74b4 80%,#1d5c8f 100%)}
.hero-caption{position:absolute;left:99px;top:194px;width:335px;height:121px;background:rgba(40,40,40,.78);text-align:center;color:var(--white);padding-top:20px}
.hero-caption strong{display:block;font-size:29px;font-weight:700;letter-spacing:.5px}
.hero-caption span{display:block;font-size:28px;font-weight:400;letter-spacing:1px}
.slider-arrow{position:absolute;top:427px;width:24px;height:24px;border-radius:50%;background:rgba(255,255,255,.55)}

/* ticker */
.ticker-band{position:absolute;left:0;top:727px;width:1200px;height:85px;background:var(--blue)}
.ticker{position:absolute;left:99px;top:26px;width:1002px;height:36px;background:var(--white);border-radius:3px;display:flex;align-items:center;justify-content:space-between;padding:0 10px;font-size:10.5px;color:var(--blue-deep);white-space:nowrap}
.ticker .up{color:var(--up)}
.ticker .down{color:var(--down)}
.ticker-arrow{color:var(--blue-deep);font-size:9px;letter-spacing:-2px;flex:none}

/* section headings */
.section-title{position:absolute;left:0;width:1200px;display:flex;justify-content:center;align-items:center;gap:16px}
.section-title .dot{width:62px;height:62px;border-radius:50%;background:linear-gradient(135deg,#dfe8f2,#9fb5cc)}
.section-title h2{font-weight:400;font-size:30px;color:#444}

/* features */
.tile{position:absolute;overflow:hidden}
.tile .tile-label{position:absolute;left:0;right:0;top:50%;transform:translateY(-50%);text-align:center;color:var(--white);font-size:14.5px;font-weight:600}
.tile-large .tile-caption{position:absolute;left:0;right:0;bottom:0;height:96px;background:rgba(31,109,179,.88);color:var(--white);padding:12px 18px}
.tile-large h3{font-size:14.5px;font-weight:600;margin-bottom:8px}
.tile-large p{font-size:11.5px;line-height:19px}

/* about */
.about{position:absolute;left:0;top:1378px;width:1200px;height:315px;
  background:
    radial-gradient(ellipse 300px 160px at 150px 280px,rgba(20,50,85,.55),rgba(20,50,85,0) 75%),
    radial-gradient(ellipse 300px 160px at 1050px 280px,rgba(20,50,85,.5),rgba(20,50,85,0) 75%),
    linear-gradient(180deg,#2f679a,#1d4f7e 60%,#23598b)}
.about .section-title h2{color:var(--white)}
.about .dot{background:linear-gradient(135deg,#ffffff,#b8cde3)}
.about-text{position:absolute;left:0;top:134px;width:1200px;text-align:center;color:var(--white);font-size:12.5px;font-style:italic;line-height:26px}
.btn{position:absolute;left:503px;width:194px;height:52px;line-height:52px;text-align:center;color:var(--white);font-size:14px;font-weight:600;background:linear-gradient(#2d7cc4,#1b5f9f);border-radius:3px}

/* blog */
.blog-card{position:absolute;top:1833px;width:242px;text-align:center}
.blog-thumb{height:156px}
.blog-card h4{margin-top:14px;font-size:14.5px;font-weight:600;color:#444}
.blog-card time{display:block;margin-top:4px;font-size:11px;font-style:italic;color:var(--blue)}

/* registration */
.register{position:absolute;left:0;top:2084px;width:1200px;height:295px;background:linear-gradient(180deg,#f2f4f6 0%,#d6dde4 45%,#c9d1d8 55%,#eef1f3 100%)}
.register .section-title h2{color:var(--blue);font-size:30px}
.register-text{position:absolute;left:0;top:126px;width:1200px;text-align:center;font-size:12.5px;color:#444;line-height:27px}

/* footer */
.site-footer{position:absolute;left:0;top:2379px;width:1200px;height:87px;background:var(--footer);color:var(--white)}
.footer-mark{position:absolute;left:99px;top:21px;width:46px;height:46px;border-radius:50%;background:#cfd8e2}
.footer-links{position:absolute;left:166px;top:20px;font-size:11px}
.footer-copy{position:absolute;left:166px;top:45px;font-size:10.5px}
.connect{position:absolute;left:868px;top:35px;font-size:10.5px}
.social{position:absolute;top:28px;width:28px;height:28px;border:1.5px solid #fff;border-radius:50%}
</style>
</head>
<body>

<header class="site-header">
  <div class="brand"><span class="brand-mark"></span><span class="brand-name">Harbourline</span></div>
  <div class="brand-sub">INCORPORATION LIMITED</div>

  <div class="contact-item" style="left:572px">
    <svg width="22" height="36" viewBox="0 0 22 36"><rect x="1.5" y="1.5" width="19" height="33" rx="3" fill="none" stroke="#1f6db3" stroke-width="3"/><rect x="5" y="6" width="12" height="21" fill="#1f6db3"/><circle cx="11" cy="30.5" r="1.8" fill="#1f6db3"/></svg>
    <div><div class="contact-label">Phone:</div><div class="contact-value">020 5550 1742</div></div>
  </div>
  <div class="contact-item" style="left:756px">
    <svg width="24" height="36" viewBox="0 0 24 36"><path d="M12 1C5.9 1 1 5.9 1 12c0 8 11 23 11 23s11-15 11-23C23 5.9 18.1 1 12 1z" fill="#1f6db3"/><circle cx="12" cy="12" r="4.5" fill="#fff"/></svg>
    <div><div class="contact-label">Location:</div>
      <div class="contact-address">harbourlineincorporation,Harbourline Incorporation Limited<br>12 Lantern Quay Road Central Hong Kong SAR</div></div>
  </div>
</header>

<nav class="main-nav">
  <div class="nav-item active">Home</div>
  <div class="nav-item" style="left:313px">About us<span class="caret"></span></div>
  <div class="nav-item" style="left:499px">International payments<span class="caret"></span></div>
  <div class="nav-item" style="left:784px">Client application<span class="caret"></span></div>
  <div class="nav-item" style="left:1029px">Contact us</div>
</nav>
<ul class="dropdown">
  <li>Making Payments</li><li>Customer Protection</li><li>No Obligation</li><li>Corporate Clients</li><li>Private Clients</li>
</ul>

<section class="hero" role="img" aria-label="Harbour city skyline with tall towers, mountains and blue water under a clear sky">
  <div class="hero-caption"><strong>NEW FOREX &amp; FUND</strong><span>REMITTANCE..!</span></div>
  <span class="slider-arrow" style="left:1043px"></span>
  <span class="slider-arrow" style="left:1075px"></span>
</section>

<div class="ticker-band">
  <div class="ticker">
    <span class="ticker-arrow">◀◀</span>
    <span>NORTH BRIDGE HLD NBH 80.70 <span class="up">▾0.77 ▾0.88%</span></span>
    <span>NORTH BRIDGE HLD NBH 80.70 <span class="down">▴0.77 ▴0.88%</span></span>
    <span>NORTH BRIDGE HLD NBH 80.70 <span class="up">▾0.77 ▾0.88%</span></span>
    <span>NORTH BRIDGE HLD NBH 80.70 <span class="down">▴0.77 ▴0.88%</span></span>
    <span class="ticker-arrow">▶▶</span>
  </div>
</div>

<div class="section-title" style="top:862px"><span class="dot"></span><h2>Our Features</h2></div>

<div class="tile tile-large" style="left:99px;top:957px;width:506px;height:370px;background:radial-gradient(ellipse 160px 120px at 250px 180px,rgba(150,165,180,.45),rgba(150,165,180,0) 75%),linear-gradient(180deg,#f3f5f7,#dfe5ea 70%,#c9d3dc)" role="img" aria-label="Hands exchanging a banknote through a smartphone in front of a pale city">
  <div class="tile-caption">
    <h3>International Money Transfer</h3>
    <p>Sed ut perspiciatis unde omnis iste natus error sit voluptatem accusantium doloremque laudantium, totam rem aperiam, eaque ipsa quae ab...</p>
  </div>
</div>
<div class="tile" style="left:617px;top:957px;width:236px;height:177px;background:radial-gradient(ellipse 90px 60px at 120px 120px,rgba(150,180,200,.45),rgba(150,180,200,0) 75%),linear-gradient(160deg,#3a79b3,#1c5487)" role="img" aria-label="Stacks of coins on a blue financial chart"><span class="tile-label">Foreign Exchange</span></div>
<div class="tile" style="left:866px;top:957px;width:235px;height:177px;background:radial-gradient(ellipse 80px 90px at 118px 60px,rgba(25,45,75,.55),rgba(25,45,75,0) 75%),linear-gradient(160deg,#4a84b8,#1f4e7c)" role="img" aria-label="Businessman in a suit holding a glowing chart"><span class="tile-label">Paying &amp; Receiving Agency</span></div>
<div class="tile" style="left:617px;top:1147px;width:236px;height:180px;background:linear-gradient(180deg,#1d5e9a 0%,#2a78bd 55%,#0f3f6e 100%)" role="img" aria-label="Blue stock market data graph"><span class="tile-label">Praesentium voluptatum</span></div>
<div class="tile" style="left:866px;top:1147px;width:235px;height:180px;background:radial-gradient(ellipse 60px 90px at 205px 120px,rgba(20,40,65,.5),rgba(20,40,65,0) 75%),linear-gradient(180deg,#5a8cb8,#2a5a86)" role="img" aria-label="Businessman looking over the city from an office window"><span class="tile-label">Deleniti atque corrupti</span></div>

<section class="about" role="img" aria-label="Blue-tinted city skyline background">
  <div class="section-title" style="top:47px"><span class="dot"></span><h2>About Us</h2></div>
  <p class="about-text">Harbourline is a leading provider of international payment services and foreign exchange to corporations and individuals covering most of<br>the world including;&nbsp; throughout Asia, South America, and Europe...</p>
  <div class="btn" style="top:210px">Click Read More Info</div>
</section>

<div class="section-title" style="top:1733px"><span class="dot"></span><h2>Latest blog</h2></div>

<article class="blog-card" style="left:99px"><div class="blog-thumb" role="img" aria-label="Businessman holding a tablet over a city" style="background:linear-gradient(160deg,#c9d3dc,#6f7f8e)"></div><h4>Accusantium doloremqu</h4><time>Posted on 28 February 2016</time></article>
<article class="blog-card" style="left:352px"><div class="blog-thumb" role="img" aria-label="Modern towers on a waterfront under a blue sky" style="background:linear-gradient(180deg,#4f8fd0,#a9c6de 70%,#7f8f9c)"></div><h4>Accusantium doloremqu</h4><time>Posted on 28 February 2016</time></article>
<article class="blog-card" style="left:606px"><div class="blog-thumb" role="img" aria-label="Businessman touching a digital market chart" style="background:linear-gradient(160deg,#12263d,#2e5f8f)"></div><h4>Accusantium doloremqu</h4><time>Posted on 28 February 2016</time></article>
<article class="blog-card" style="left:859px"><div class="blog-thumb" role="img" aria-label="Business meeting at a desk with a laptop and coffee" style="background:linear-gradient(160deg,#d8d3cc,#6c6560)"></div><h4>Accusantium doloremqu</h4><time>Posted on 28 February 2016</time></article>

<section class="register" role="img" aria-label="Pale misty city skyline reflected in water">
  <div class="section-title" style="top:42px"><span class="dot"></span><h2>Client Registration</h2></div>
  <p class="register-text">Coupled with our excellent customer service, highly competitive rates and in depth market knowledge we provide a simple, reliable and<br>cost effective service to all of our clients.</p>
  <div class="btn" style="top:203px">Click to Register</div>
</section>

<footer class="site-footer">
  <span class="footer-mark"></span>
  <div class="footer-links">HOME &nbsp;| &nbsp;ABOUT US &nbsp;| &nbsp;INTERNATIONAL PAYMENTS &nbsp;| &nbsp;CLIENT APPLICATION &nbsp;| &nbsp;CONTACT US</div>
  <div class="footer-copy">COPYRIGHTS@HARBOURLINEINCORPORATION.2016 | ALLRIGHTS RESERVED.</div>
  <div class="connect">CONNECT WITH US:</div>
  <span class="social" style="left:972px"></span>
  <span class="social" style="left:1006px"></span>
  <span class="social" style="left:1040px"></span>
  <span class="social" style="left:1074px"></span>
</footer>

</body>
</html>
```